Corporate brochure design 4 pages

Hi,

We are a real estate company based in Europe.

We have almost finalized a rebranding.

We are developing a brand book guidelines (still on working process) to help you undertstand the look and feel of our new CI. I would like to receive proposals of design for a corporate brochure template. I need to receive the Indesign files with full ownership rights to be able to adapt all our documentation with this template.
Regarding the images, you can take gabaris on www.pelvarimages.example. I will be able to take them afterwards.

There will be 4 pages. you will receive the 4 pages on pdf for your consideration with our (almost) actual layout.

- 1st page: cover
- 2nd page: company presentation in french and english
- 3rd page: some market data + graph
- 4th page: 2 retail centers presentation.

In the template, i need to have:
- the paragraph styles in order
- 2 different masters with top/bottom/page number aso.

Please feel free to ask any other questions.

best regards,
Updates

I would like to precise tha t we are active on the commercial real estate sector:

- office transactions (rent /sales)
- property management of administrative and business buildings
- Valuation of properties
- Capital markets (investment advices for selling building)

Industry/Entity Type

Real Estate

Colors

Designer to choose colors to be used in the design.

```html
<!DOCTYPE html>
<html lang="fr">
<head>
<meta charset="utf-8">
<title>Estavia Partners – A propos de nous</title>
<link rel="stylesheet" href="https://fonts.googleapis.com/css2?family=Arimo:wght@400;700&family=Raleway:wght@300&display=swap">
<style>
  :root {
    --ink: #111111;
    --orange: #f26a1b;
    --orange-soft: #f9c9a8;
    --paper: #ffffff;
    --photo-dark: #2d3238;
    --photo-mid: #6f7a82;
    --photo-light: #c9d1d4;
  }
  html, body { margin: 0; padding: 0; overflow: hidden; background: var(--paper); }
  .page {
    position: relative; width: 848px; height: 1200px; overflow: hidden;
    background: var(--paper); color: var(--ink);
    font-family: "Arimo", Arial, sans-serif;
  }
  .swoosh { position: absolute; left: 0; width: 848px; }
  .swoosh--top { top: 0; height: 90px; }
  .swoosh--bottom { bottom: 0; height: 70px; z-index: 3; }
  .column { position: absolute; top: 84px; width: 366px; }
  .column--fr { left: 47px; }
  .column--en { left: 446px; width: 362px; }
  .column__title { margin: 0; font-weight: 700; font-size: 21px; letter-spacing: 0.2px; }
  .column__subtitle {
    margin: 2px 0 12px; font-family: "Raleway", Arial, sans-serif; font-weight: 300;
    font-size: 24px; letter-spacing: 0.5px;
  }
  .column p { margin: 0; font-size: 15.4px; line-height: 19px; text-align: justify; hyphens: none; }
  .column .lead { font-weight: 700; margin-bottom: 7px; }
  .column p + p:not(.lead) { text-indent: 50px; }
  .column .lead + p { text-indent: 50px; }
  .team-photo {
    position: absolute; left: 0; top: 640px; width: 848px; height: 520px;
    background: linear-gradient(160deg, var(--photo-light) 0%, var(--photo-mid) 45%, var(--photo-dark) 100%);
  }
  .photo-edge { position: absolute; left: 0; top: 628px; width: 848px; height: 46px; z-index: 2; }
  .team-names {
    position: absolute; right: 34px; top: 1040px; z-index: 2; margin: 0; padding: 0; list-style: none;
    text-align: right; color: var(--paper); font-weight: 700; font-size: 16px; line-height: 20px;
  }
</style>
</head>
<body>
<div class="page">
  <svg class="swoosh swoosh--top" viewBox="0 0 848 90" preserveAspectRatio="none" aria-hidden="true">
    <path d="M0 0 H848 V22 C600 10 260 28 0 62 Z" fill="var(--paper)"/>
    <path d="M0 40 C250 14 560 6 848 18 V30 C560 20 260 34 0 66 Z" fill="var(--ink)"/>
    <path d="M0 62 C260 36 560 24 848 30 V38 C560 32 260 46 0 74 Z" fill="var(--orange)"/>
  </svg>

  <section class="column column--fr" lang="fr">
    <h1 class="column__title">A PROPOS DE NOUS</h1>
    <h2 class="column__subtitle">UNE ÉQUIPE</h2>
    <p class="lead">Proposer des services de qualité répondant parfaitement à vos attentes est notre ambition. Elle est partagée par tous les membres de notre équipe.</p>
    <p>Notre connaissance du marché luxembourgeois, nos compétences et notre engagement dans les missions qui nous sont confiées font de Estavia Partners l'acteur majeur de l'immobilier d'entreprise au Grand-Duché. Nous sommes fiers de cette position et nous travaillons tous les jours pour la conserver.</p>
    <p>Viser l'excellence suppose de savoir améliorer sans cesse nos prestations pour répondre le plus précisément à vos besoins. Venez nous consulter, vous constaterez que nos collaborateurs prennent le temps de vous écouter pour bien comprendre votre demande. Leur professionnalisme, leur savoir-faire et leur mobilisation nous permettront de trouver la solution.</p>
  </section>

  <section class="column column--en" lang="en">
    <h1 class="column__title">ABOUT US</h1>
    <h2 class="column__subtitle">A TEAM</h2>
    <p class="lead">Our ambition is to offer quality services that perfectly meet your expectations. This ambition is shared by all members of the team.</p>
    <p>Thanks to our knowledge of the Luxembourg market, our skills and our commitment to the missions entrusted to us, Estavia Partners is the undisputed leader in commercial real estate in the Grand Duchy. We are proud of this position and work hard to deserve it every day.</p>
    <p>Targeting excellence means the constant improvement of our services in order to more accurately meet your needs. When you meet with us, you will find that our employees take the necessary time to listen to you and to correctly understand your need. Their professionalism, know-how and mobilisation will ensure that we find the right solution.</p>
  </section>

  <svg class="photo-edge" viewBox="0 0 848 46" preserveAspectRatio="none" aria-hidden="true">
    <path d="M0 0 H848 V18 C560 8 260 14 0 40 Z" fill="var(--paper)"/>
    <path d="M0 30 C260 6 560 2 848 10 V18 C560 10 260 16 0 40 Z" fill="var(--orange)"/>
    <path d="M0 40 C260 16 560 10 848 18 V28 C560 20 260 26 0 46 Z" fill="var(--ink)"/>
  </svg>

  <div class="team-photo" role="img" aria-label="Group photograph of the four partners in dark suits in a modern glass office"></div>

  <ul class="team-names">
    <li>Julien Morvaux</li>
    <li>Thomas Lerdal</li>
    <li>Paul Kessring</li>
    <li>Erik Valdemar</li>
  </ul>

  <svg class="swoosh swoosh--bottom" viewBox="0 0 848 70" preserveAspectRatio="none" aria-hidden="true">
    <path d="M0 6 C260 30 560 34 848 20 V70 H0 Z" fill="var(--paper)"/>
    <path d="M0 0 C260 26 560 30 848 14 V30 C560 44 260 40 0 16 Z" fill="var(--ink)"/>
    <path d="M0 22 C260 46 560 50 848 36 V46 C560 60 260 56 0 32 Z" fill="var(--orange)"/>
  </svg>
</div>
</body>
</html>
```